Lip Balm Label Design

Design a label for a Lavender-Mint lip balm. We make high-quality natural essential oil products. Please use the old label as an example of what exists. The label should include purple. The final design should be eye-catching and distinct. The file should be in an AI file.

Here is the information that should be included on the label:
1) ingredients:Theobroma Cacao (Cocoa) Seed Butter, Theobroma grandiflorum Ultra Refined Butter, beesewax, Calendula Officinalis Flower Oil, Prunus Amygdalus Dulcis (Sweet Almond) Oil, cetyl alcohol and Tocopherol. Lavandula Angustifolia (Lavender) Oil and Mentha Piperita (Peppermint) Oil.

2) www.kelsoroothaven.com

3) Brand name and logo: K. Elso Aromatherapy (logo is attached- you can use with form)

```html
<!DOCTYPE html>
<html lang="en">
<head>
<meta charset="UTF-8">
<title>Lavender-Mint Lip Balm Label</title>
<link rel="stylesheet" href="https://fonts.googleapis.com/css2?family=Cormorant+Garamond:wght@400;500&family=Playfair+Display:wght@800&family=Pathway+Gothic+One&display=swap">
<style>
  :root {
    --page: #ffffff;
    --label-purple: #7367e3;
    --brand-green: #6e9f3f;
    --pill-white: #ffffff;
    --flavour-purple: #6b5fd8;
    --panel-lilac: #e3e0fe;
    --ingredient-ink: #1d1b26;
    --ingredient-accent: #8a7fe8;
    --url-ink: #ece9ff;
    --sprig-purple: #a78ae8;
    --sprig-green: #8fb45a;
  }
  html, body {
    margin: 0;
    width: 1200px;
    height: 1000px;
    overflow: hidden;
    background: var(--page);
  }
  .label {
    position: absolute;
    left: 207px;
    top: 205px;
    width: 786px;
    height: 590px;
    background: var(--label-purple);
    overflow: hidden;
  }
  .label-face {
    position: absolute;
    left: 98px;
    top: -98px;
    width: 590px;
    height: 786px;
    transform: rotate(90deg);
  }
  .brand {
    position: absolute;
    left: 17px;
    top: 40px;
    width: 556px;
    height: 110px;
    display: flex;
    align-items: center;
    gap: 22px;
  }
  .brand-dot {
    width: 96px;
    height: 96px;
    border-radius: 50%;
    background: var(--brand-green);
    flex: none;
  }
  .brand-name {
    font-family: "Cormorant Garamond", serif;
    font-weight: 500;
    font-size: 40px;
    line-height: 1;
    color: var(--brand-green);
    white-space: nowrap;
  }
  .sprig-art {
    position: absolute;
    left: 54px;
    top: 186px;
    width: 482px;
    height: 317px;
    border-radius: 40px;
    background: radial-gradient(ellipse at 50% 90%, rgba(143,180,90,0.45), rgba(167,138,232,0.35) 55%, rgba(115,103,227,0) 80%);
  }
  .flavour-pill {
    position: absolute;
    left: 151px;
    top: 184px;
    width: 288px;
    height: 75px;
    border-radius: 20px;
    background: var(--pill-white);
    display: flex;
    align-items: center;
    justify-content: center;
  }
  .flavour-name {
    font-family: "Playfair Display", serif;
    font-weight: 800;
    font-size: 46px;
    color: var(--flavour-purple);
    transform: scaleX(0.62);
    white-space: nowrap;
    letter-spacing: 0.5px;
  }
  .ingredients {
    position: absolute;
    left: 32px;
    top: 577px;
    width: 526px;
    height: 138px;
    box-sizing: border-box;
    padding: 12px 13px;
    border-radius: 22px;
    background: var(--panel-lilac);
  }
  .ingredients p {
    margin: 0;
    font-family: "Pathway Gothic One", sans-serif;
    font-size: 19.5px;
    line-height: 28.5px;
    color: var(--ingredient-ink);
    text-align: justify;
  }
  .ingredients-heading {
    color: var(--ingredient-accent);
  }
  .site-url {
    position: absolute;
    left: 32px;
    top: 722px;
    width: 526px;
    text-align: center;
    font-family: "Cormorant Garamond", serif;
    font-weight: 400;
    font-size: 33px;
    color: var(--url-ink);
    letter-spacing: 0.5px;
  }
</style>
</head>
<body>
  <div class="label">
    <div class="label-face">
      <div class="brand">
        <span class="brand-dot"></span>
        <span class="brand-name">K. Elso Aromatherapy</span>
      </div>

      <div class="sprig-art" role="img" aria-label="Illustrated wreath of lavender sprigs with green leaves"></div>

      <div class="flavour-pill">
        <span class="flavour-name">LAVENDER-MINT</span>
      </div>

      <div class="ingredients">
        <p><span class="ingredients-heading">INGREDIENTS:</span> Theobroma Cacao (Cocoa) Seed Butter, Theobroma grandiflorum Ultra Refined Butter, beesewax, Calendula Officinalis Flower Oil, Prunus Amygdalus Dulcis (Sweet Almond) Oil, cetyl alcohol and Tocopherol. Lavandula Angustifolia (Lavender) Oil and Mentha Piperita (Peppermint) Oil.</p>
      </div>

      <div class="site-url">www.kelsoroothaven.com</div>
    </div>
  </div>
</body>
</html>
```